Business Card Design for Occupational Medicine Start Up Company

We need to design a professional business card. We are a healthcare company providing occupational medicine services to blue collar industries. We are professional, efficient and high quality service providers.

Target Market(s)

Blue Collar Industry: Shipbuilding, Ports, Trucking Companies; The Executives and Safety Officers for these companies

Industry/Entity Type

Healthcare

Contact Information for Business Card

Logo, Name, Title, Email, Phone

Other font styles liked:
• Please match our Brand Guide

Requirements
Must have
• Our Company Colors and Logo

```html
<!DOCTYPE html>
<html lang="en">
<head>
<meta charset="utf-8">
<title>Crewline Health — Business Card</title>
<link href="https://fonts.googleapis.com/css2?family=Montserrat:wght@400;500;600;700&display=swap" rel="stylesheet">
<style>
  :root {
    --stage: #2b2b2b;
    --navy: #2f3076;
    --navy-deep: #2c2d6e;
    --lilac: #7478d8;
    --sky: #3aa3dd;
    --amber: #e9a83a;
    --paper: #f4f4f2;
    --white: #ffffff;
  }
  * { box-sizing: border-box; margin: 0; padding: 0; }
  html, body {
    width: 1200px; height: 1200px; overflow: hidden;
    background: var(--stage);
    font-family: "Montserrat", sans-serif;
  }
  .card {
    position: absolute;
    left: 304px;
    width: 592px; height: 348px;
    border-radius: 22px;
    overflow: hidden;
  }
  /* Back side */
  .card-back {
    top: 200px;
    background: var(--navy);
  }
  .back-brand {
    position: absolute; left: 0; right: 0; top: 132px;
    display: flex; align-items: center; justify-content: center; gap: 14px;
  }
  .back-brand .mark {
    width: 34px; height: 34px; border-radius: 50%;
    background: var(--lilac);
  }
  .back-brand .name {
    font-weight: 700; font-size: 34px; letter-spacing: 1px;
    color: var(--lilac);
  }
  .back-url {
    position: absolute; left: 0; right: 0; top: 300px;
    text-align: center;
    font-size: 15px; font-weight: 500; letter-spacing: 1.6px;
    color: var(--white);
  }
  .back-url .blue { color: var(--sky); }
  .back-url .amber { color: var(--amber); }

  /* Front side */
  .card-front {
    top: 640px;
    background: var(--paper);
  }
  .front-wave { position: absolute; inset: 0; }
  .holder {
    position: absolute; right: 42px; top: 24px; text-align: right;
  }
  .holder-name {
    font-weight: 600; font-size: 25px; letter-spacing: 0.5px;
    color: var(--sky); line-height: 1.1;
  }
  .holder-title {
    font-weight: 500; font-size: 15px; color: var(--white); margin-top: 3px;
  }
  .front-brand {
    position: absolute; left: 40px; top: 150px;
    display: flex; align-items: center; gap: 12px;
  }
  .front-brand .mark {
    width: 40px; height: 40px; border-radius: 50%; background: var(--amber);
  }
  .front-brand .name {
    font-weight: 700; font-size: 27px; color: var(--navy);
  }
  .contact {
    position: absolute; list-style: none;
    font-size: 15px; color: var(--navy-deep); font-weight: 500;
  }
  .contact li {
    display: flex; align-items: center; gap: 12px; height: 21.5px;
  }
  .contact svg { width: 14px; height: 14px; flex: none; }
  .contact-main { left: 50px; top: 248px; }
  .contact-address { left: 330px; top: 269px; }
  .contact-address li { align-items: flex-start; }
  .contact-address .lines { line-height: 21.5px; margin-top: -4px; }
</style>
</head>
<body>

<section class="card card-back" aria-label="Card back">
  <div class="back-brand">
    <span class="mark"></span>
    <span class="name">CREWLINE HEALTH</span>
  </div>
  <p class="back-url">www.<span class="blue">crewline</span>health<span class="amber">clinics</span>.com</p>
</section>

<section class="card card-front" aria-label="Card front">
  <svg class="front-wave" viewBox="0 0 592 348" preserveAspectRatio="none" aria-hidden="true">
    <path d="M0,0 H592 V88 C520,100 470,98 420,80 C340,48 260,20 170,20 C100,20 40,35 0,52 Z" fill="var(--navy)"/>
    <path d="M0,50 C60,22 150,10 260,24 C300,30 320,36 296,34 C220,24 120,30 0,62 Z" fill="var(--sky)"/>
    <path d="M55,62 C150,30 280,32 370,62 C440,86 500,104 592,90" fill="none" stroke="var(--amber)" stroke-width="4"/>
  </svg>

  <div class="holder">
    <p class="holder-name">DANIEL MARSH</p>
    <p class="holder-title">Senior Doctor</p>
  </div>

  <div class="front-brand">
    <span class="mark"></span>
    <span class="name">CREWLINE HEALTH</span>
  </div>

  <ul class="contact contact-main">
    <li>
      <svg viewBox="0 0 16 16"><path d="M2 6 C2 3 14 3 14 6 L12 7 L10 5.5 H6 L4 7 Z M4 8 H12 L13 13 H3 Z" fill="var(--sky)"/></svg>
      555-014-2290
    </li>
    <li>
      <svg viewBox="0 0 16 16"><rect x="1" y="3" width="14" height="10" fill="var(--navy)"/><path d="M1 3 L8 9 L15 3" fill="none" stroke="var(--white)" stroke-width="1.3"/></svg>
      care@crewlinehealth.com
    </li>
    <li>
      <svg viewBox="0 0 16 16"><circle cx="8" cy="8" r="6.5" fill="none" stroke="var(--amber)" stroke-width="1.5"/><ellipse cx="8" cy="8" rx="3" ry="6.5" fill="none" stroke="var(--amber)" stroke-width="1.2"/><path d="M1.5 8 H14.5" stroke="var(--amber)" stroke-width="1.2"/></svg>
      www.crewlinehealth.com
    </li>
  </ul>

  <ul class="contact contact-address">
    <li>
      <svg viewBox="0 0 16 16"><path d="M8 1 C4.5 1 2.5 3.5 2.5 6.3 C2.5 10 8 15 8 15 C8 15 13.5 10 13.5 6.3 C13.5 3.5 11.5 1 8 1 Z" fill="var(--amber)"/><circle cx="8" cy="6.2" r="2" fill="var(--paper)"/></svg>
      <span class="lines">480 Harbor Avenue, Suite 210<br>Portside, State 20418</span>
    </li>
  </ul>
</section>

</body>
</html>
```